Upland Bird Hunting Preserve and Pointing Dog kennel

Need Price packages outlined for the bird hunting business. List the kennel and that we provide training and dogs for sale.
The preserve is "Tall Heron Provisions" the dog kennel is "Pine Hollow Setters"
1/2 Day Upland Field Hunts: 5 Pheasants $120
7 Chukar $125
Continental Hunt 12 Pheasants $325 includes meal, minimum 12 hunters
Guides available $100

Target Market(s)

upland bird hunters

Industry/Entity Type

hunting, outdoor

Colors
EE7325
F08F49
F5BC92
FAE3D3
FDF4ED

```html
<!DOCTYPE html>
<html lang="en">
<head>
<meta charset="utf-8">
<title>Tall Heron Provisions – Hunting Packages</title>
<link href="https://fonts.googleapis.com/css2?family=Cinzel:wght@500;600;700&family=Inter:wght@400;700&display=swap" rel="stylesheet">
<style>
  :root{
    --orange-deep:#EE7325;
    --orange:#F08F49;
    --orange-soft:#F5BC92;
    --peach:#FAE3D3;
    --cream:#FDF4ED;
    --ink:#000;
    --paper:#fff;
    --backdrop:#d6d7d9;
  }
  *{margin:0;padding:0;box-sizing:border-box}
  html,body{width:986px;height:1200px;overflow:hidden;background:var(--backdrop)}
  .flyer{position:absolute;left:29px;top:0;width:927px;height:1200px;background:var(--ink);color:var(--paper);font-family:"Inter",Arial,sans-serif;overflow:hidden}
  .abs{position:absolute;line-height:1}
  .brand{left:0;width:100%;text-align:center;font-family:"Cinzel",Georgia,serif;white-space:nowrap}
  .brand-name{top:33px;font-size:38px;font-weight:600}
  .brand-town{top:77px;font-size:32px;font-weight:500}
  .preserve-band{left:137px;top:119px;width:653px;height:35px;background:linear-gradient(90deg,rgba(240,143,73,0) 0%,var(--orange) 17%,var(--orange) 83%,rgba(240,143,73,0) 100%);text-align:center;font-family:"Cinzel",Georgia,serif;font-weight:700;font-size:25px;line-height:37px;color:#1a1a1a}
  .section-title{top:173px;left:0;width:100%;text-align:center;font-weight:700;font-size:26px;letter-spacing:8.5px;white-space:nowrap}
  .section-rule{top:185px;height:2px;width:126px;background:linear-gradient(90deg,rgba(238,115,37,0),var(--orange-deep))}
  .section-rule.right{transform:scaleX(-1)}
  .packages{left:68px;top:210px;width:520px}
  .package h2{font-size:30px;font-weight:700;line-height:34px;letter-spacing:-.3px;white-space:nowrap}
  .package p{font-size:29px;line-height:33px;font-weight:400;letter-spacing:-.4px;white-space:nowrap}
  .package-divider{height:1px;width:325px;margin:10px 0 12px;background:linear-gradient(90deg,#555,#333 80%,transparent)}
  .photo{border:6px solid var(--paper)}
  .dog-photo{left:587px;top:243px;width:282px;height:216px;transform:rotate(-8.8deg);background:linear-gradient(160deg,#d9ae5a 0%,#b98d42 35%,#5b5550 55%,#3c3a38 70%,#c39a4f 100%)}
  .rule-orange{left:0;width:100%;height:8px;background:var(--orange)}
  .group-photo{left:0;top:539px;width:100%;height:322px;background:linear-gradient(180deg,#b9a582 0%,#9d8a6c 22%,#6f6470 40%,#c98a4e 52%,#7a5e4c 62%,#c2b7a6 72%,#8d7a66 84%,#4a4038 100%)}
  .truck-photo{left:70px;top:827px;width:419px;height:217px;background:linear-gradient(90deg,#e8a63c 0%,#c9a46a 30%,#5c5450 52%,#a8343a 60%,#d9b487 78%,#9a8a78 100%)}
  .kennel-name{left:520px;top:948px;width:360px;text-align:center;font-family:"Cinzel",Georgia,serif;font-size:22px;font-weight:600;color:var(--orange);white-space:nowrap}
  .kennel-rule{left:602px;top:1009px;width:208px;height:4px;background:var(--orange)}
  .kennel-town{left:520px;top:1024px;width:360px;text-align:center;font-family:"Cinzel",Georgia,serif;font-size:21px;font-weight:500;color:var(--orange);white-space:nowrap}
  .services{left:229px;top:1068px;font-size:29px;line-height:33px;letter-spacing:-.5px;white-space:nowrap}
  .services strong{color:var(--orange);font-weight:700}
  .contact-rule{left:0;top:1138px;width:100%;height:1px;background:var(--paper)}
  .contact-bar{left:0;top:1142px;width:100%;height:58px;background:var(--orange);color:#111;text-align:center;font-size:24px;line-height:44px;letter-spacing:-.3px;white-space:nowrap}
  .contact-bar b{font-weight:700}
</style>
</head>
<body>
<main class="flyer">
  <h1 class="abs brand brand-name">TALL HERON PROVISIONS, LLC</h1>
  <div class="abs brand brand-town">Marlow Creek, MO</div>
  <div class="abs preserve-band">LICENSED SHOOTING PRESERVE</div>

  <span class="abs section-rule" style="left:122px"></span>
  <h2 class="abs section-title">HUNTING PACKAGES</h2>
  <span class="abs section-rule right" style="left:678px"></span>

  <section class="abs packages">
    <div class="package">
      <h2>½ DAY UPLAND FIELD HUNTS</h2>
      <p>5 Pheasants — $120</p>
      <p>7 Chukar - $125</p>
    </div>
    <div class="package-divider"></div>
    <div class="package">
      <h2>CONTINENTAL PHEASANT HUNT</h2>
      <p>12 Pheasants — $325 (includes meal)</p>
      <p>12 Hunter Minimum</p>
    </div>
    <div class="package-divider"></div>
    <div class="package">
      <h2>GUIDES AVAILABLE</h2>
      <p>$100 per half day</p>
    </div>
  </section>

  <div class="abs photo dog-photo" role="img" aria-label="Photo of a pointing dog standing in dry golden field grass"></div>

  <div class="abs rule-orange" style="top:531px"></div>
  <div class="abs group-photo" role="img" aria-label="Photo of a hunting party lined up behind a fallen log with the day's pheasants, a black dog beside them"></div>
  <div class="abs rule-orange" style="top:861px"></div>

  <div class="abs photo truck-photo" role="img" aria-label="Photo of hunters in blaze orange with a white dog and birds on a truck tailgate"></div>

  <div class="abs kennel-name">PINE HOLLOW SETTERS</div>
  <div class="abs kennel-rule"></div>
  <div class="abs kennel-town">BIRCH BEND, MO</div>

  <div class="abs services">
    <p>Professional <strong>Dog Training</strong> available</p>
    <p>Puppies and started dogs <strong>for sale!</strong></p>
  </div>

  <div class="abs contact-rule"></div>
  <div class="abs contact-bar"><b>CONTACT- (DALE MERCER:</b> 555-014-2273)</div>
</main>
</body>
</html>
```